Clearing Your Slate - Banner Ad for TH Website

I need a banner ad for a book I'm selling.

The book is about Clearing Your Slate, that is a County Court Judgment, from a credit report.

I have two websites. I want the banner ad to appear on
www.thorncaldwell.co.uk

It will then link to the new site: https://debtslatecleaner.co.uk/

The first site already has a lot of traffic from visitors wanting to remove a CCJ. The purpose of that first site was originally for visitors to become clients of the law firm. However, most visitors can't afford legal advice and so I'd like to offer them the book instead.

I would like to see designs that use the colour green. The final design should communicate financial freedom, simplicity and trustworthiness.

Target Market(s)

Individuals who have discovered a CCJ on their credit report

Industry/Entity Type

Law

Font styles to use
Sans Serif

Colors
0054AA
0677BA
7BADD7
CADEEF
E8F1F8
0094D4
00A9DD
6FCCEA
C7EBF8
E9F6FB
00AB8E
00BBA5
67D7C9
C6EFE9
E9F9F6

Requirements
Must have
• Must fit at the end of a blog article, such as this one https://www.thorncaldwell.co.uk/ccj-wrong-address/

```html
<!DOCTYPE html>
<html lang="en">
<head>
<meta charset="utf-8">
<title>Clearing Your Slate – Banner</title>
<link rel="stylesheet" href="https://fonts.googleapis.com/css2?family=Montserrat:wght@300;400;600;800&family=Oswald:wght@600;700&family=Cinzel:wght@500&display=swap">
<style>
  :root {
    --bg-dark: #4b4b4b;
    --bg-mid: #707070;
    --bg-light: #8d8d8d;
    --white: #ffffff;
    --green: #3fb53a;
    --red: #e0262b;
    --ink: #1d1d1d;
    --cover-shadow: rgba(0,0,0,0.35);
  }
  html, body {
    margin: 0;
    padding: 0;
    overflow: hidden;
    background: var(--bg-dark);
  }
  .banner {
    position: relative;
    width: 1200px;
    height: 500px;
    overflow: hidden;
    font-family: "Montserrat", sans-serif;
    color: var(--white);
  }
  .banner__photo {
    position: absolute;
    inset: 0;
    background:
      radial-gradient(ellipse 260px 300px at 400px 330px, rgba(190,170,120,0.55), rgba(120,110,90,0.25) 60%, transparent 80%),
      radial-gradient(ellipse 160px 140px at 420px 90px, rgba(90,140,60,0.5), transparent 75%),
      linear-gradient(90deg, var(--bg-dark) 0%, var(--bg-mid) 45%, var(--bg-light) 70%, var(--bg-mid) 100%);
  }
  .banner__shade {
    position: absolute;
    inset: 0;
    background: linear-gradient(90deg, rgba(0,0,0,0.35) 0%, rgba(0,0,0,0.15) 50%, transparent 75%);
  }
  .banner__accent {
    position: absolute;
    inset: 0;
  }
  .banner__copy {
    position: absolute;
    left: 98px;
    top: 104px;
    width: 630px;
  }
  .headline {
    margin: 0;
    font-size: 56px;
    line-height: 1.08;
    letter-spacing: -0.5px;
  }
  .headline__strong {
    display: block;
    font-weight: 800;
  }
  .headline__light {
    display: block;
    font-weight: 300;
  }
  .intro {
    margin: 22px 0 0;
    font-size: 17.5px;
    line-height: 1.75;
    font-weight: 400;
  }
  .intro strong { font-weight: 800; }
  .cta {
    display: block;
    margin-top: 26px;
    width: 196px;
    height: 50px;
    line-height: 50px;
    text-align: center;
    background: var(--green);
    color: var(--white);
    font-size: 18px;
    font-weight: 400;
    letter-spacing: 0.3px;
    text-decoration: none;
  }
  .book {
    position: absolute;
    left: 784px;
    top: 35px;
    width: 306px;
    height: 425px;
    background: var(--white);
    box-shadow: 6px 8px 18px var(--cover-shadow), inset 8px 0 6px -4px rgba(0,0,0,0.12);
    color: var(--ink);
    text-align: center;
    font-family: "Oswald", sans-serif;
  }
  .book > * {
    position: absolute;
    left: 0;
    right: 0;
    margin: 0 auto;
  }
  .book__kicker {
    top: 12px;
    font-size: 30px;
    font-weight: 700;
    line-height: 1.2;
    letter-spacing: 0.5px;
  }
  .book__title-box {
    top: 48px;
    width: 200px;
    box-sizing: border-box;
    border: 4px solid var(--red);
    color: var(--red);
    font-size: 40px;
    font-weight: 700;
    line-height: 46px;
    letter-spacing: 1px;
  }
  .book__big {
    top: 104px;
    color: var(--red);
    font-size: 96px;
    font-weight: 700;
    line-height: 1;
    letter-spacing: 1px;
  }
  .book__tagline {
    top: 218px;
    width: 250px;
    font-family: "Montserrat", sans-serif;
    font-size: 8.5px;
    font-weight: 600;
    line-height: 1.4;
    color: var(--ink);
  }
  .book__tagline span { color: var(--red); }
  .book__art {
    top: 282px;
    width: 200px;
    height: 82px;
    background: linear-gradient(90deg, #3a3a3a 0%, #5a5a5a 35%, #e9eef3 50%, #dfe8f1 100%);
    border-radius: 4px;
  }
  .book__author {
    top: 372px;
    font-family: "Cinzel", serif;
    font-size: 24px;
    font-weight: 500;
    line-height: 1.2;
    letter-spacing: 2px;
  }
  .book__role {
    top: 402px;
    font-family: "Montserrat", sans-serif;
    color: var(--red);
    font-size: 10px;
    font-weight: 600;
    line-height: 1.2;
    letter-spacing: 2px;
  }
</style>
</head>
<body>
  <div class="banner">
    <div class="banner__photo" role="img" aria-label="Young green plant growing out of a glass jar filled with coins, on a soft grey background"></div>
    <div class="banner__shade"></div>

    <svg class="banner__accent" width="1200" height="500" viewBox="0 0 1200 500" aria-hidden="true">
      <polygon points="1162,0 1182,0 954,500 934,500" fill="var(--white)"/>
      <polygon points="1182,0 1200,0 1200,500 954,500" fill="var(--green)"/>
    </svg>

    <div class="banner__copy">
      <h1 class="headline">
        <span class="headline__strong">Need help</span>
        <span class="headline__light">removing a CCJ?</span>
      </h1>
      <p class="intro"><strong>“Clearing Your Slate”</strong> explains in simple language the steps<br>you need to take to get the CCJ removed.</p>
      <a class="cta" href="https://debtslatecleaner.co.uk/">CLICK HERE</a>
    </div>

    <div class="book">
      <div class="book__kicker">CLEARING</div>
      <div class="book__title-box">YOUR</div>
      <div class="book__big">SLATE</div>
      <p class="book__tagline">A SIMPLE JARGON-FREE GUIDE TO <span>REMOVING OF A COUNTY COURT JUDGMENT FROM YOUR CREDIT RECORD.</span></p>
      <div class="book__art" role="img" aria-label="Cartoon businessman breaking free from a ball and chain marked CCJ"></div>
      <div class="book__author">MARTIN HALE</div>
      <div class="book__role">SOLICITOR</div>
    </div>
  </div>
</body>
</html>
```